Kettleby Twins Playing Cards

We are wanting a cool design for a playing card that includes our logo(s). I will attach our two logos, we are open to using either one of them or another version of them. I will also attach some pictures of card decks to use for inspiration. These are just decks that we have seen from other artists that we liked. We are located in West Texas so although not necessary, a Sotol or Agave or cactus or quail (bird) or some sort of sunset would pay homage to our surroundings. I realize the examples are all very different, but those are just some decks that we like! Thank you!

```html
<!DOCTYPE html>
<html lang="en">
<head>
<meta charset="utf-8">
<title>Kettleby Twins Playing Cards</title>
<link rel="stylesheet" href="https://fonts.googleapis.com/css2?family=Oswald:wght@500&family=Rye&display=swap">
<style>
  :root {
    --stage: #2f2f2f;
    --card-black: #050607;
    --royal-blue: #1470d6;
    --mid-blue: #0c56aa;
    --deep-blue: #062c5e;
    --silver-light: #f1eee8;
    --silver: #d4d0c8;
    --silver-dark: #8d8a84;
    --silver-shadow: #55534f;
  }
  html, body {
    margin: 0;
    padding: 0;
    width: 1200px;
    height: 900px;
    overflow: hidden;
    background: var(--stage);
  }
  .canvas {
    width: 1200px;
    height: 900px;
    display: flex;
    justify-content: center;
    align-items: center;
    gap: 90px;
  }
  .card {
    position: relative;
    width: 380px;
    height: 540px;
    border-radius: 26px;
    background: var(--card-black);
    box-shadow: 0 18px 40px rgba(0,0,0,0.45);
    box-sizing: border-box;
    padding: 14px;
  }

  /* Card back */
  .back-field {
    position: relative;
    width: 100%;
    height: 100%;
    border-radius: 16px;
    overflow: hidden;
    background:
      radial-gradient(ellipse at 50% 50%, rgba(0,0,0,0) 40%, rgba(3,14,32,0.55) 100%),
      repeating-radial-gradient(circle at 50% 50%, var(--royal-blue) 0 14px, var(--mid-blue) 14px 18px, var(--royal-blue) 18px 30px, var(--deep-blue) 30px 33px);
  }
  .back-frame {
    position: absolute;
    inset: 12px;
    border: 2px solid var(--card-black);
    border-radius: 10px;
    pointer-events: none;
  }
  .back-frame::after {
    content: "";
    position: absolute;
    inset: 6px;
    border: 1px solid rgba(5,6,7,0.7);
    border-radius: 6px;
  }
  .back-brand {
    position: absolute;
    left: 50%;
    top: 50%;
    transform: translate(-50%, -50%);
    display: flex;
    align-items: center;
    gap: 12px;
    padding: 16px 24px;
    background: var(--card-black);
    border: 2px solid var(--silver-dark);
    border-radius: 10px;
  }
  .brand-dot {
    width: 16px;
    height: 16px;
    border-radius: 50%;
    background: var(--silver);
  }
  .brand-name {
    font-family: "Oswald", sans-serif;
    font-weight: 500;
    font-size: 30px;
    line-height: 1;
    letter-spacing: 1px;
    text-transform: uppercase;
    color: var(--silver);
    white-space: nowrap;
  }

  /* Card face */
  .face-frame {
    position: relative;
    width: 100%;
    height: 100%;
    border: 2px solid var(--silver-dark);
    border-radius: 16px;
    box-sizing: border-box;
  }
  .frame-tick {
    position: absolute;
    background: var(--silver-dark);
  }
  .tick-h { width: 2px; height: 12px; }
  .tick-v { width: 12px; height: 2px; }
  .tick-top-a { top: -7px; left: 30%; }
  .tick-top-b { top: -7px; left: 70%; }
  .tick-bottom-a { bottom: -7px; left: 30%; }
  .tick-bottom-b { bottom: -7px; left: 70%; }
  .tick-left-a { left: -7px; top: 33%; }
  .tick-left-b { left: -7px; top: 67%; }
  .tick-right-a { right: -7px; top: 33%; }
  .tick-right-b { right: -7px; top: 67%; }

  .index {
    position: absolute;
    width: 44px;
    display: flex;
    flex-direction: column;
    align-items: center;
    gap: 6px;
  }
  .index-top { top: 18px; left: 16px; }
  .index-bottom { bottom: 18px; right: 16px; transform: rotate(180deg); }
  .index-rank {
    font-family: "Rye", serif;
    font-size: 42px;
    line-height: 1;
    color: var(--silver);
  }
  .index-suit { width: 30px; height: 30px; fill: var(--silver); }
  .face-pip {
    position: absolute;
    left: 50%;
    top: 50%;
    width: 240px;
    height: 250px;
    transform: translate(-50%, -50%);
  }
</style>
</head>
<body>
  <main class="canvas">
    <section class="card card-back" aria-label="Card back">
      <div class="back-field" role="img" aria-label="Dense blue and black paisley and floral ornament pattern">
        <div class="back-frame"></div>
      </div>
      <div class="back-brand">
        <span class="brand-dot"></span>
        <span class="brand-name">Kettleby Twins</span>
      </div>
    </section>

    <section class="card card-face" aria-label="Ace of clubs">
      <div class="face-frame">
        <span class="frame-tick tick-h tick-top-a"></span>
        <span class="frame-tick tick-h tick-top-b"></span>
        <span class="frame-tick tick-h tick-bottom-a"></span>
        <span class="frame-tick tick-h tick-bottom-b"></span>
        <span class="frame-tick tick-v tick-left-a"></span>
        <span class="frame-tick tick-v tick-left-b"></span>
        <span class="frame-tick tick-v tick-right-a"></span>
        <span class="frame-tick tick-v tick-right-b"></span>

        <div class="index index-top">
          <span class="index-rank">A</span>
          <svg class="index-suit" viewBox="0 0 30 30" aria-hidden="true">
            <circle cx="15" cy="8" r="6.5"/>
            <circle cx="8" cy="17" r="6.5"/>
            <circle cx="22" cy="17" r="6.5"/>
            <path d="M13.5 14 h3 q0 10 5 15 h-13 q5 -5 5 -15 z"/>
          </svg>
        </div>

        <svg class="face-pip" viewBox="0 0 240 250" role="img" aria-label="Ornate silver club illustration with paisley and feather detailing">
          <defs>
            <linearGradient id="silver-sheen" x1="0" y1="0" x2="1" y2="1">
              <stop offset="0" stop-color="var(--silver-light)"/>
              <stop offset="0.45" stop-color="var(--silver)"/>
              <stop offset="0.75" stop-color="var(--silver-dark)"/>
              <stop offset="1" stop-color="var(--silver-shadow)"/>
            </linearGradient>
          </defs>
          <g fill="url(#silver-sheen)">
            <circle cx="120" cy="62" r="56"/>
            <circle cx="62" cy="140" r="56"/>
            <circle cx="178" cy="140" r="56"/>
            <path d="M108 110 h24 q2 80 46 134 h-116 q44 -54 46 -134 z"/>
          </g>
        </svg>

        <div class="index index-bottom">
          <span class="index-rank">A</span>
          <svg class="index-suit" viewBox="0 0 30 30" aria-hidden="true">
            <circle cx="15" cy="8" r="6.5"/>
            <circle cx="8" cy="17" r="6.5"/>
            <circle cx="22" cy="17" r="6.5"/>
            <path d="M13.5 14 h3 q0 10 5 15 h-13 q5 -5 5 -15 z"/>
          </svg>
        </div>
      </div>
    </section>
  </main>
</body>
</html>
```